Business card design for a dynamic IT consulting company

We need a business card design for a young firm, specialized in the Telecommunications/Consulting industry. The name of the company is Quindor and Partners Business Consulting Ltd. (Short name: Quindor and Partnes)
Quindor = solve read reverse, so we aim to be uncomplicated and solution-oriented. The small pipe in our logo is also related to the word solve. So we need a new business card design, which is simple, eye catching and something non traditional (I would probably prefer a square shaped design rather than a rectangle, but open for suggestions). Attached our logo.

Target Market(s)

Usually our customers are Tier1 Telecoms providers (Q-Netra, Palorix, etc) and their executives.

Industry/Entity Type

Business

Contact Information for Business Card

Name: Bence Tolnavari
Email: b.tolnavari@quindor.hu
Web: www.quindor.hu
Mobile: +36 30 518 2769
Title: Managing Director

Optional:
Company name: Quindor and Partners Ltd.
Address: 1087 Budapest, Tolvenka str. 28/C, Hungary

Font styles to use
Other font styles liked:
• helveticaneue_medium, Prime Regular are used now.

Colors

Designer to choose colors to be used in the design.

Requirements
Must have
• I would like to have a 2 sided design.
Nice to have
• I thought if we make the logo a bit bigger (without the company name), that could go to the back with the company name below. I though, if the pipe in the logo is somehow touchable on the business card, would be nice and unique.

```html
<!DOCTYPE html>
<html lang="en">
<head>
<meta charset="utf-8">
<title>Quindor and Partners – Business Card</title>
<link rel="stylesheet" href="https://fonts.googleapis.com/css2?family=Roboto:wght@400;500&display=swap">
<style>
  :root {
    --page-bg: #e8e6e2;
    --card-white: #f7f7f7;
    --charcoal: #3a3b3d;
    --charcoal-deep: #26272a;
    --logo-grey: #6d6e71;
    --magenta: #c23fae;
    --magenta-light: #d65cc4;
    --cyan: #1fb3d8;
    --text-light: #f2f2f2;
    --font-main: "Roboto", "Helvetica Neue", Arial, sans-serif;
  }
  * { box-sizing: border-box; margin: 0; padding: 0; }
  html, body {
    width: 1200px; height: 780px; overflow: hidden;
    background: var(--page-bg);
    font-family: var(--font-main);
  }
  .card-sheet {
    position: relative; width: 1200px; height: 780px;
    display: flex; align-items: center; justify-content: center; gap: 40px;
  }
  .card {
    position: relative; width: 540px; height: 310px;
    border-radius: 4px; overflow: hidden;
    box-shadow: 0 10px 28px rgba(0,0,0,.22);
  }

  /* Front */
  .card--front { background: var(--card-white); }
  .front__top { position: absolute; left: 0; top: 0; width: 540px; height: 165px; }
  .company-name {
    position: absolute; left: 34px; top: 66px;
    display: flex; align-items: center; gap: 12px;
    color: var(--logo-grey); font-weight: 400; font-size: 32px; letter-spacing: .3px;
    white-space: nowrap;
  }
  .company-name__square { width: 12px; height: 12px; background: var(--magenta); flex: none; }
  .front__pattern {
    position: absolute; right: 0; top: 0; width: 150px; height: 165px;
    background: linear-gradient(135deg, #c9eef8 0%, #e7c1df 55%, #d5d5d6 100%);
  }
  .front__bottom {
    position: absolute; left: 0; top: 165px; width: 540px; height: 145px;
    background: linear-gradient(180deg, var(--charcoal) 0%, var(--charcoal-deep) 100%);
  }
  .name-band {
    position: absolute; left: 0; top: 165px; width: 360px; height: 36px;
    background: var(--magenta);
    display: flex; align-items: center; padding-left: 34px; gap: 14px;
    color: #fff; white-space: nowrap;
  }
  .name-band__name { font-size: 19px; font-weight: 500; }
  .name-band__divider { width: 1px; height: 20px; background: rgba(255,255,255,.75); }
  .name-band__title { font-size: 13px; font-weight: 400; }
  .contact {
    position: absolute; left: 34px; top: 214px;
    display: flex; gap: 26px; color: var(--text-light); font-size: 12.5px; line-height: 1.6;
  }
  .contact__list { list-style: none; }
  .contact__item { display: flex; align-items: center; gap: 8px; }
  .contact__icon {
    width: 16px; height: 16px; border: 1.3px solid var(--cyan); border-radius: 50%;
    display: flex; align-items: center; justify-content: center; flex: none;
  }

  /* Back */
  .card--back {
    background: radial-gradient(ellipse at 40% 35%, #4a4b4e 0%, var(--charcoal) 45%, var(--charcoal-deep) 100%);
  }
  .back__pattern {
    position: absolute; right: 0; top: 0; width: 200px; height: 230px;
    background: linear-gradient(160deg, rgba(255,255,255,0) 0%, rgba(0,0,0,.18) 100%);
  }
  .back__name {
    position: absolute; left: 0; right: 0; top: 100px;
    display: flex; align-items: center; justify-content: center; gap: 14px;
    color: var(--text-light); font-size: 36px; font-weight: 400; letter-spacing: .5px;
    white-space: nowrap;
  }
  .back__square { width: 13px; height: 13px; background: var(--cyan); flex: none; }
  .web-band {
    position: absolute; left: 0; top: 236px; width: 540px; height: 36px;
    background: linear-gradient(90deg, var(--magenta) 0%, var(--magenta-light) 100%);
    border-top: 3px solid #8f2e80; border-bottom: 3px solid #8f2e80;
    display: flex; align-items: center; justify-content: center;
    color: var(--text-light); font-size: 14px; letter-spacing: 4px;
  }
</style>
</head>
<body>
<main class="card-sheet">

  <section class="card card--front" aria-label="Business card front">
    <div class="front__top">
      <div class="company-name"><span class="company-name__square"></span>Quindor &amp; Partners</div>
    </div>
    <div class="front__bottom"></div>
    <div class="front__pattern" role="img" aria-label="Decorative field of small cyan, magenta and grey squares"></div>
    <div class="name-band">
      <span class="name-band__name">Bence Tolnavari</span>
      <span class="name-band__divider"></span>
      <span class="name-band__title">Managing Director</span>
    </div>
    <div class="contact">
      <ul class="contact__list">
        <li>1087 Budapest</li>
        <li>Tolvenka str. 28/C, Hungary</li>
      </ul>
      <ul class="contact__list">
        <li class="contact__item">
          <span class="contact__icon">
            <svg width="9" height="9" viewBox="0 0 10 10"><rect x="2.5" y="0.5" width="5" height="9" rx="1" fill="none" stroke="#1fb3d8" stroke-width="1.2"/></svg>
          </span>+36 30 518 2769</li>
        <li class="contact__item">
          <span class="contact__icon">
            <svg width="9" height="9" viewBox="0 0 10 10"><rect x="0.7" y="2" width="8.6" height="6" fill="none" stroke="#1fb3d8" stroke-width="1.1"/><path d="M0.7 2 L5 5.5 L9.3 2" fill="none" stroke="#1fb3d8" stroke-width="1.1"/></svg>
          </span>b.tolnavari@quindor.hu</li>
        <li class="contact__item">
          <span class="contact__icon">
            <svg width="9" height="9" viewBox="0 0 10 10"><circle cx="5" cy="5" r="4.3" fill="none" stroke="#1fb3d8" stroke-width="1.1"/><ellipse cx="5" cy="5" rx="1.8" ry="4.3" fill="none" stroke="#1fb3d8" stroke-width="1"/><path d="M0.7 5 H9.3" stroke="#1fb3d8" stroke-width="1"/></svg>
          </span>www.quindor.hu</li>
      </ul>
    </div>
  </section>

  <section class="card card--back" aria-label="Business card back">
    <div class="back__pattern" role="img" aria-label="Faint decorative squares in dark grey"></div>
    <div class="back__name"><span class="back__square"></span>Quindor &amp; Partners</div>
    <div class="web-band">www.quindor.hu</div>
  </section>

</main>
</body>
</html>
```